Business Card Design

We are a commercial real estate brokerage in San Francisco, leasing office buildings downtown.
I would like a clean, elegant look. Simple but powerful .

Industry/Entity Type

Business

Contact Information for Business Card

Derek Holloway
lic# 07258143
415.555.0172
derek@velt-commercial.example
velt-commercial.example

```html
<!DOCTYPE html>
<html lang="en">
<head>
<meta charset="utf-8">
<title>Velt Commercial – Business Card</title>
<link rel="stylesheet" href="https://fonts.googleapis.com/css2?family=PT+Sans:wght@400;700&display=swap">
<style>
  :root {
    --backdrop: #e6dcc6;
    --card-dark: #2b2b2b;
    --card-light: #ffffff;
    --skyline-tone: #3f3f3f;
    --brand-slate: #8a96ad;
    --text-light: #f2f2f2;
    --text-dark: #2b2b2b;
  }
  html, body {
    margin: 0;
    width: 1200px;
    height: 510px;
    overflow: hidden;
    background: var(--backdrop);
    font-family: "PT Sans", sans-serif;
  }
  .canvas {
    position: relative;
    width: 1200px;
    height: 510px;
  }
  .card {
    position: absolute;
    top: 132px;
    width: 418px;
    height: 245px;
    border-radius: 12px;
    overflow: hidden;
    background: var(--card-dark);
    box-shadow: 0 6px 14px rgba(0,0,0,0.25);
  }
  .card--front { left: 158px; }
  .card--back { left: 625px; }

  .light-band {
    position: absolute;
    top: 0;
    bottom: 0;
    width: 114px;
    background: var(--card-light);
  }
  .card--front .light-band { right: 0; }
  .card--back .light-band { left: 0; }

  .skyline-area {
    position: absolute;
    bottom: 0;
    height: 48px;
    background: linear-gradient(to bottom, rgba(63,63,63,0), var(--skyline-tone) 55%);
  }
  .card--front .skyline-area { left: 0; width: 304px; }
  .card--back .skyline-area { left: 114px; right: 0; }

  .brand {
    position: absolute;
    display: flex;
    align-items: center;
    gap: 10px;
  }
  .brand__mark {
    width: 14px;
    height: 14px;
    background: var(--brand-slate);
  }
  .brand__name {
    font-weight: 700;
    font-size: 18px;
    letter-spacing: 0.5px;
    color: var(--brand-slate);
    white-space: nowrap;
    text-transform: uppercase;
  }
  .card--front .brand { left: 58px; top: 110px; }
  .card--back .brand {
    left: 57px;
    top: 122px;
    transform: translate(-50%, -50%) rotate(-90deg);
  }
  .card--back .brand__name { font-size: 15px; }

  .website {
    position: absolute;
    right: 57px;
    top: 122px;
    transform: translate(50%, -50%) rotate(90deg);
    font-size: 10px;
    color: var(--text-dark);
    white-space: nowrap;
  }

  .contact {
    position: absolute;
    left: 203px;
    top: 86px;
    color: var(--text-light);
  }
  .contact__name {
    font-size: 13px;
    line-height: 16px;
    margin: 0 0 9px;
    font-weight: 400;
  }
  .contact__line {
    font-size: 9.5px;
    line-height: 15.5px;
    margin: 0;
  }
</style>
</head>
<body>
<main class="canvas">
  <section class="card card--front">
    <div class="brand">
      <span class="brand__mark"></span>
      <span class="brand__name">Velt Commercial</span>
    </div>
    <div class="skyline-area" role="img" aria-label="City skyline silhouette"></div>
    <div class="light-band">
      <span class="website">velt-commercial.example</span>
    </div>
  </section>

  <section class="card card--back">
    <div class="light-band">
      <div class="brand">
        <span class="brand__mark"></span>
        <span class="brand__name">Velt Commercial</span>
      </div>
    </div>
    <div class="skyline-area" role="img" aria-label="City skyline silhouette"></div>
    <div class="contact">
      <p class="contact__name">Derek Holloway</p>
      <p class="contact__line">lic# 07258143</p>
      <p class="contact__line">415.555.0172</p>
      <p class="contact__line">derek@velt-commercial.example</p>
    </div>
  </section>
</main>
</body>
</html>
```